New travel store signage for Marlow Journeys to attract luxury travellers.

Hello,
We are looking to change the signage of our stores. The signage must include the following:
1. Marlow Journeys Logo (attached)
2. The text...The Travel & Cruise Experts
3. Brand Colours ( Fb0196, 412266, d41d84 and ffffff)
Please note the signage design must be central and only cover two thirds of the store front. We have also attached an image of one of our new stores which might be helpful when preparing a mock up.

We are looking for a quick turnaround on this, making a decision within 48 hours.

Target Market(s)

Retail

Industry/Entity Type

Travel Agency

Font styles to use
Other font styles liked:
• Radley

Colors
E54698
E96AAD
F1A4CE
F9D9EA
FCEFF6
6B429C
8869AF
B7A5CE
E3DAEB
F3F0F8

Requirements
Must have
• Hello, We are looking to change the signage of our stores. The signage must include the following: 1. Marlow Journeys Logo (attached) 2. The text...The Travel & Cruise Experts 3. Brand Colours ( Fb0196, 412266, d41d84 and ffffff) Please note the signage design must be central and only cover two thirds of the store front.
Should not have
• different colour or fonts. Gradient design.

```html
<!DOCTYPE html>
<html lang="en">
<head>
<meta charset="utf-8">
<title>Marlow Journeys Store Sign</title>
<link href="https://fonts.googleapis.com/css2?family=Radley&display=swap" rel="stylesheet">
<style>
  :root {
    --backdrop: #dcdcdc;
    --sign-white: #ffffff;
    --brand-magenta: #d41d84;
    --brand-purple: #412266;
  }
  html, body {
    margin: 0;
    padding: 0;
    overflow: hidden;
  }
  .canvas {
    width: 1200px;
    height: 919px;
    background: var(--backdrop);
    position: relative;
    overflow: hidden;
  }
  .fascia {
    position: absolute;
    left: 64px;
    top: 394px;
    width: 1072px;
    height: 132px;
  }
  .fascia-shape {
    position: absolute;
    inset: 0;
    width: 100%;
    height: 100%;
    display: block;
  }
  .fascia-shape .panel-white { fill: var(--sign-white); }
  .fascia-shape .panel-magenta { fill: var(--brand-magenta); }
  .brand-name {
    position: absolute;
    left: 0;
    width: 330px;
    top: 0;
    height: 132px;
    display: flex;
    align-items: center;
    justify-content: center;
    gap: 10px;
    font-family: "Radley", serif;
    font-size: 25px;
    color: var(--brand-purple);
    white-space: nowrap;
  }
  .brand-dot {
    width: 14px;
    height: 14px;
    border-radius: 50%;
    background: var(--brand-magenta);
  }
  .tagline {
    position: absolute;
    left: 360px;
    right: 0;
    top: 0;
    height: 132px;
    display: flex;
    align-items: center;
    justify-content: center;
    padding-left: 24px;
    box-sizing: border-box;
    font-family: "Radley", serif;
    font-size: 52px;
    color: var(--sign-white);
    white-space: nowrap;
  }
</style>
</head>
<body>
<div class="canvas">
  <div class="fascia">
    <svg class="fascia-shape" viewBox="0 0 1072 132" preserveAspectRatio="none" aria-hidden="true">
      <rect class="panel-white" x="0" y="0" width="1072" height="132"/>
      <polygon class="panel-magenta" points="360,0 1072,0 1072,132 360,132 329,66"/>
    </svg>
    <div class="brand-name"><span class="brand-dot"></span>Marlow Journeys</div>
    <div class="tagline">The Travel &amp; Cruise Experts</div>
  </div>
</div>
</body>
</html>
```